Computer Security FaceBook start-up design.

Should be in Harmony with https://www.quorvant.com We need a design for our facebook profile for our company Quorvant. We work at computer security consulting services and licensing offering a high technological MothGuard. A Framework That Allows any security based company to analyze / monitorize / etc. really any application with high performance and stealth based on hypervisor technologies. Our main color is RED, as you will see in our logo. The design Should our deep expertise transmit / skills on security. We would like to have MothGuard Also Represented as Lynx With an Anything That Could That remark is Iberian Lynx (if possible). Any questions are welcome :)

Industry/Entity Type

Computer Security

Requirements
Must have
• Should be in armony With https://www.quorvant.com

```html
<!DOCTYPE html>
<html lang="en">
<head>
<meta charset="utf-8">
<title>Quorvant – Memory Guard Interception</title>
<link rel="stylesheet" href="https://fonts.googleapis.com/css2?family=Open+Sans:wght@400;600;700&display=swap">
<style>
  :root {
    --white: #ffffff;
    --paper: #f4f7fa;
    --brand-red: #e0303a;
    --headline-blue: #1d5f9c;
    --ink: #111111;
    --wave-deep: #0f5aa8;
    --wave-mid: #2d86cf;
    --wave-light: #9cc8ea;
    --visual-dark: #0b3a72;
    --visual-mid: #2479c4;
    --visual-light: #bcd9f0;
  }
  * { margin: 0; padding: 0; box-sizing: border-box; }
  html, body { width: 1200px; height: 451px; overflow: hidden; background: var(--white); }
  body { font-family: "Open Sans", Arial, sans-serif; }

  .cover {
    position: relative;
    width: 1200px;
    height: 451px;
    overflow: hidden;
    background: linear-gradient(90deg, var(--white) 0%, var(--paper) 40%, var(--white) 100%);
  }

  .hero-visual {
    position: absolute;
    left: 440px;
    top: 30px;
    width: 760px;
    height: 390px;
    background:
      radial-gradient(circle at 62% 50%, rgba(255,255,255,0.55) 0 70px, rgba(120,190,240,0.35) 71px 160px, transparent 161px),
      linear-gradient(90deg, rgba(255,255,255,1) 0%, var(--visual-light) 18%, var(--visual-mid) 45%, var(--visual-dark) 80%, var(--visual-mid) 100%);
  }

  .waves { position: absolute; inset: 0; width: 1200px; height: 451px; }

  .brand {
    position: absolute;
    left: 46px;
    top: 172px;
    display: flex;
    align-items: center;
    gap: 12px;
  }
  .brand-mark {
    width: 28px;
    height: 28px;
    background: var(--brand-red);
  }
  .brand-name {
    font-size: 27px;
    font-weight: 600;
    color: var(--ink);
    letter-spacing: 0.5px;
  }

  .headline {
    position: absolute;
    left: 40px;
    top: 270px;
    line-height: 1.15;
  }
  .headline-lead {
    display: block;
    font-size: 31px;
    font-weight: 400;
    color: var(--brand-red);
  }
  .headline-main {
    display: block;
    font-size: 34px;
    font-weight: 400;
    color: var(--headline-blue);
  }

  .powered {
    position: absolute;
    left: 42px;
    top: 378px;
    display: flex;
    align-items: center;
    gap: 32px;
  }
  .powered-label {
    font-size: 22px;
    font-weight: 700;
    color: var(--ink);
  }
  .partner {
    display: flex;
    align-items: center;
    gap: 8px;
  }
  .partner-mark {
    width: 22px;
    height: 22px;
    border-radius: 50%;
    background: var(--brand-red);
  }
  .partner-name {
    font-size: 22px;
    font-weight: 600;
    color: var(--brand-red);
  }
</style>
</head>
<body>
<main class="cover">
  <div class="hero-visual" role="img" aria-label="Hand touching a glowing blue security interface with a padlock surrounded by digital icons"></div>

  <svg class="waves" viewBox="0 0 1200 451" aria-hidden="true">
    <path d="M0,0 H1200 V18 C1000,6 700,30 420,36 C260,40 120,30 0,14 Z" fill="var(--wave-deep)"/>
    <path d="M0,14 C120,30 260,40 420,36 C700,30 1000,6 1200,18 V30 C1000,22 720,58 430,62 C250,64 110,50 0,30 Z" fill="var(--wave-mid)"/>
    <path d="M0,30 C110,50 250,64 430,62 C720,58 1000,22 1200,30 V38 C1000,32 720,72 430,76 C250,78 110,64 0,44 Z" fill="var(--wave-light)" opacity="0.6"/>

    <path d="M0,432 C260,412 520,406 760,392 C940,382 1090,352 1200,318 V451 H0 Z" fill="var(--wave-light)" opacity="0.7"/>
    <path d="M0,446 C280,428 560,424 800,410 C960,400 1100,372 1200,340 V451 H0 Z" fill="var(--wave-mid)"/>
    <path d="M300,451 C560,440 820,430 980,412 C1080,400 1150,384 1200,368 V451 Z" fill="var(--wave-deep)"/>
  </svg>

  <div class="brand">
    <span class="brand-mark"></span>
    <span class="brand-name">QUORVANT</span>
  </div>

  <h1 class="headline">
    <span class="headline-lead">State of the Art</span>
    <span class="headline-main">Memory Guard Interception</span>
  </h1>

  <div class="powered">
    <span class="powered-label">Powered by</span>
    <span class="partner">
      <span class="partner-mark"></span>
      <span class="partner-name">MothGuard</span>
    </span>
  </div>
</main>
</body>
</html>
```